Business Card Design Project

We need a business card for a new technology services company. We develop software and implement software packages for our business customers and although we will begin with just one or two service offerings, our service offerings will expand over time. Our name comes from the an author, KL Barrow, and his "idea" was that opportunity should be based on ability and achievement, not on social status.

We would like to see a design that is standard in its size and shape, but stands apart in its dramatic color contrasts. The card should not use too many colors - the colors used in the background should highlight the brilliant blues of the logo (see attachment) to dramatic effect. The background should not be white.

If necessary, you can change the color of the words "KL Barrow", but not the word "Idea".

Card size should be U.S. standard 2 inches by 3.5 inches and provide for 1/8 inch bleed area on each side.

We need a design for both sides of the business card, one side communicating the company logo and contact information, the other side being purely graphical, incorporating the logo but no other information.

Contact Information Required:
Kate Brook
KateBrook@klbarrowvista.com
614-387-2259

Target Market(s)

Business executives

Industry/Entity Type

Software

Requirements
Must have
• It must have the full company logo on one side, and at least the graphic element of the logo on the other. Either that or the full logo on both.
Nice to have
• It would be nice to have a design that could work without needing two different textures. For example, it would be nice if the entire card could be shiny, not just parts of the card.

It would also be nice if texture is something we could add later.
Should not have
• The card should not use the color green.

```html
<!DOCTYPE html>
<html lang="en">
<head>
<meta charset="utf-8">
<title>KL Barrow Vista — Business Card</title>
<link rel="stylesheet" href="https://fonts.googleapis.com/css2?family=Roboto:wght@300;400;700&display=swap">
<style>
  :root {
    --page-bg: #ecedef;
    --sky-light: #dfe6f1;
    --sky-mid: #bccbe2;
    --sky-deep: #a9bcd9;
    --brand-blue: #1a8ccc;
    --ink: #1e2228;
    --divider: #6d7480;
    --card-shadow: rgba(20, 30, 50, 0.22);
  }
  * { box-sizing: border-box; margin: 0; padding: 0; }
  html, body {
    width: 1200px;
    height: 750px;
    overflow: hidden;
    background: var(--page-bg);
    font-family: "Roboto", Arial, sans-serif;
  }
  .sheet {
    position: relative;
    width: 1200px;
    height: 750px;
  }
  .card {
    position: absolute;
    top: 226px;
    width: 520px;
    height: 298px;
    overflow: hidden;
    box-shadow: 0 6px 18px var(--card-shadow);
  }
  .card--front { left: 50px; }
  .card--back { left: 630px; }
  .card__sky {
    position: absolute;
    inset: 0;
    background:
      radial-gradient(ellipse at 25% 30%, var(--sky-light) 0%, transparent 55%),
      radial-gradient(ellipse at 75% 75%, var(--sky-light) 0%, transparent 50%),
      linear-gradient(160deg, var(--sky-mid) 0%, var(--sky-deep) 55%, var(--sky-mid) 100%);
  }
  .wordmark {
    position: absolute;
    display: flex;
    align-items: center;
    gap: 14px;
    font-weight: 400;
    color: var(--brand-blue);
    letter-spacing: -1.5px;
    white-space: nowrap;
  }
  .wordmark__dot {
    display: block;
    border-radius: 50%;
    background: var(--brand-blue);
  }
  .card--front .wordmark {
    left: 70px;
    top: 150px;
    font-size: 44px;
  }
  .card--front .wordmark__dot { width: 34px; height: 34px; }
  .card--back .wordmark {
    left: 60px;
    top: 116px;
    font-size: 46px;
  }
  .card--back .wordmark__dot { width: 40px; height: 40px; }
  .contact {
    position: absolute;
    left: 0;
    top: 226px;
    width: 100%;
    display: flex;
    align-items: center;
  }
  .contact__name {
    width: 238px;
    text-align: right;
    padding-right: 14px;
    font-weight: 700;
    font-size: 16px;
    color: var(--brand-blue);
    letter-spacing: 0.3px;
    align-self: flex-end;
    margin-bottom: 2px;
  }
  .contact__divider {
    width: 1px;
    height: 48px;
    background: var(--divider);
  }
  .contact__lines {
    list-style: none;
    padding-left: 12px;
    font-size: 13px;
    color: var(--ink);
  }
  .contact__line {
    display: flex;
    align-items: center;
    gap: 7px;
    line-height: 24px;
  }
  .contact__icon { width: 11px; height: 11px; fill: var(--ink); }
</style>
</head>
<body>
<main class="sheet">
  <section class="card card--front" aria-label="Business card front">
    <div class="card__sky" role="img" aria-label="Soft blue sky with light clouds"></div>
    <div class="wordmark">
      <span class="wordmark__text">KL Barrow Vista</span>
      <span class="wordmark__dot" aria-hidden="true"></span>
    </div>
    <div class="contact">
      <p class="contact__name">KATE BROOK</p>
      <span class="contact__divider" aria-hidden="true"></span>
      <ul class="contact__lines">
        <li class="contact__line">
          <svg class="contact__icon" viewBox="0 0 24 24" aria-hidden="true"><path d="M6.6 10.8a15.1 15.1 0 0 0 6.6 6.6l2.2-2.2a1 1 0 0 1 1-.25 11.4 11.4 0 0 0 3.6.57 1 1 0 0 1 1 1V20a1 1 0 0 1-1 1A17 17 0 0 1 3 4a1 1 0 0 1 1-1h3.5a1 1 0 0 1 1 1c0 1.25.2 2.45.57 3.57a1 1 0 0 1-.25 1z"/></svg>
          <span>614-387-2259</span>
        </li>
        <li class="contact__line">
          <svg class="contact__icon" viewBox="0 0 24 24" aria-hidden="true"><path d="M2 5h20v14H2z M4 7v.5l8 5 8-5V7l-8 5z" fill-rule="evenodd"/></svg>
          <span>KateBrook@klbarrowvista.com</span>
        </li>
      </ul>
    </div>
  </section>

  <section class="card card--back" aria-label="Business card back">
    <div class="card__sky" role="img" aria-label="Soft blue sky with light clouds"></div>
    <div class="wordmark">
      <span class="wordmark__text">KL Barrow Vista</span>
      <span class="wordmark__dot" aria-hidden="true"></span>
    </div>
  </section>
</main>
</body>
</html>
```